Boutique town planning business needs a Business Card design

We need a business card design for a new company called The Zoning Bridgeway. We provide town planning and urban design services to government, business and community groups. We would like to see the designs use the colours in the logo (blue, deep red, green and amber), plenty of white and including black and grey in the writing. The final design should communicate collaboration, creativity and professionalism and that we are approachable.

Industry/Entity Type

Town

```html
<!DOCTYPE html>
<html lang="en">
<head>
<meta charset="utf-8">
<title>The Zoning Bridgeway – Business Card</title>
<link rel="stylesheet" href="https://fonts.googleapis.com/css2?family=Open+Sans:wght@400;600;700&display=swap">
<style>
  :root {
    --bg: #e9e7e3;
    --card-white: #ffffff;
    --card-dark: #353535;
    --band-black: #111111;
    --ink: #2b2b2b;
    --ink-soft: #6a6a6a;
    --amber: #f28a1a;
    --brand-blue: #2f8fcf;
    --white: #ffffff;
  }
  * { box-sizing: border-box; margin: 0; padding: 0; }
  html, body { width: 1057px; height: 1200px; overflow: hidden; }
  body {
    background: var(--bg);
    font-family: "Open Sans", Arial, sans-serif;
    position: relative;
  }
  .card {
    position: absolute;
    left: 98px;
    width: 860px;
    height: 491px;
    box-shadow: 0 6px 18px rgba(0,0,0,0.18);
    overflow: hidden;
  }
  /* Front */
  .card-front { top: 70px; background: var(--card-dark); }
  .front-brand {
    position: absolute; left: 0; right: 0; top: 170px;
    display: flex; align-items: center; justify-content: center; gap: 22px;
  }
  .brand-dot {
    width: 78px; height: 78px; border-radius: 50%;
    border: 5px solid var(--white);
  }
  .brand-name {
    font-weight: 700; font-size: 40px; line-height: 1.05; color: var(--white);
  }
  .front-web {
    position: absolute; left: 0; right: 0; top: 300px;
    text-align: center; color: var(--white);
    font-size: 17px; letter-spacing: 6px;
  }
  /* Back */
  .card-back { top: 640px; background: var(--card-white); }
  .back-brand {
    position: absolute; left: 360px; top: 52px;
    display: flex; align-items: center; gap: 16px;
  }
  .back-brand .brand-dot {
    width: 60px; height: 60px; border: none; background: var(--brand-blue);
  }
  .back-brand .brand-name { color: var(--ink); font-size: 32px; }
  .name-tag {
    position: absolute; left: 0; top: 168px;
    width: 250px; height: 46px; background: var(--amber);
    color: var(--white); font-weight: 600; font-size: 22px;
    letter-spacing: 2px; padding: 8px 0 0 28px;
  }
  .job-title {
    position: absolute; left: 28px; top: 222px;
    color: var(--ink); font-size: 15px; letter-spacing: 2px;
  }
  .contact-band {
    position: absolute; left: 140px; right: 0; top: 270px; height: 110px;
    background: var(--band-black);
  }
  .band-chevrons { position: absolute; left: 20px; top: 25px; }
  .contact-grid {
    position: absolute; left: 190px; top: 22px;
    display: grid; grid-template-columns: 220px 280px; row-gap: 18px;
    color: var(--white); font-size: 15px;
  }
  .contact-item { display: flex; align-items: center; gap: 10px; }
  .contact-icon {
    width: 24px; height: 24px; background: var(--white); border-radius: 3px;
    display: flex; align-items: center; justify-content: center;
  }
  .address {
    position: absolute; left: 330px; top: 405px;
    display: flex; align-items: center; gap: 10px;
    color: var(--ink-soft); font-size: 15px;
  }
  .address .contact-icon { background: var(--amber); }
</style>
</head>
<body>
  <section class="card card-front">
    <div class="front-brand">
      <span class="brand-dot"></span>
      <span class="brand-name">The<br>Zoning Bridgeway</span>
    </div>
    <p class="front-web">www.zoningbridgeway.com</p>
  </section>

  <section class="card card-back">
    <div class="back-brand">
      <span class="brand-dot"></span>
      <span class="brand-name">The<br>Zoning Bridgeway</span>
    </div>

    <div class="name-tag">MARA ELLISON</div>
    <p class="job-title">GENERAL MANAGER</p>

    <div class="contact-band">
      <svg class="band-chevrons" width="120" height="60" viewBox="0 0 120 60">
        <g fill="none" stroke="#ffffff" stroke-width="7">
          <polyline points="10,52 50,30 90,52"/>
          <polyline points="10,36 50,14 90,36"/>
          <polyline points="10,20 50,-2 90,20"/>
        </g>
      </svg>
      <div class="contact-grid">
        <div class="contact-item">
          <span class="contact-icon"><svg width="14" height="14" viewBox="0 0 24 24"><path fill="#111" d="M6.6 10.8a15 15 0 006.6 6.6l2.2-2.2a1 1 0 011-.25 11.4 11.4 0 003.6.57 1 1 0 011 1V20a1 1 0 01-1 1A17 17 0 013 4a1 1 0 011-1h3.5a1 1 0 011 1c0 1.25.2 2.45.57 3.57a1 1 0 01-.25 1z"/></svg></span>
          021 555 0148
        </div>
        <div class="contact-item">
          <span class="contact-icon"><svg width="14" height="14" viewBox="0 0 24 24"><rect x="2" y="5" width="20" height="14" fill="none" stroke="#111" stroke-width="2"/><polyline points="2,5 12,13 22,5" fill="none" stroke="#111" stroke-width="2"/></svg></span>
          hello@zoningbridgeway.com
        </div>
        <div class="contact-item">
          <span class="contact-icon"><svg width="14" height="14" viewBox="0 0 24 24"><path fill="#111" d="M6.6 10.8a15 15 0 006.6 6.6l2.2-2.2a1 1 0 011-.25 11.4 11.4 0 003.6.57 1 1 0 011 1V20a1 1 0 01-1 1A17 17 0 013 4a1 1 0 011-1h3.5a1 1 0 011 1c0 1.25.2 2.45.57 3.57a1 1 0 01-.25 1z"/></svg></span>
          021 555 0149
        </div>
        <div class="contact-item">
          <span class="contact-icon"><svg width="14" height="14" viewBox="0 0 24 24"><circle cx="12" cy="12" r="9" fill="none" stroke="#111" stroke-width="2"/><ellipse cx="12" cy="12" rx="4" ry="9" fill="none" stroke="#111" stroke-width="2"/><line x1="3" y1="12" x2="21" y2="12" stroke="#111" stroke-width="2"/></svg></span>
          www.zoningbridgeway.com
        </div>
      </div>
    </div>

    <div class="address">
      <span class="contact-icon"><svg width="14" height="14" viewBox="0 0 24 24"><path fill="#ffffff" d="M12 2a7 7 0 00-7 7c0 5 7 13 7 13s7-8 7-13a7 7 0 00-7-7zm0 9.5A2.5 2.5 0 1112 6.5a2.5 2.5 0 010 5z"/></svg></span>
      24 Harbour Lane, Level 3, Eastfield
    </div>
  </section>
</body>
</html>
```